Equipment Finance Specialist I work with companies who need the funds to buy their equipment

I would like a business card that stands out on the shelves. I want to be able to hand it to someone and say WOW. This card should have my logo.
You can put color into it I am very open on design and color

What my company does is we deal with dealerships that sell equipment such as Dump Trucks garbage trucks tractors trailers. Customers get referred to us and depending on their time in business we will ask for the following items

Companies that have been in business for more than two years we have a credit application program up to 250K . With this program we need the following items Credit application filled out(which is what I would like to be able for the customer to click on my website to get.) as well as three current month bank statements.

Deals over 250k we will need the following items

2 years business tax returns
2 years personal tax returns
Profit & Loss statement
Personal Financial Statement

what we do
100% FINANCING
SEASONAL PAYMENTS
LOAN BALLOON PAYMENTS
TRAC LEASING
LOW-INTEREST REFINANCING RATES
DEBT CONSOLIDATION

We specialize in creative financing solutions and offer a variety of reliable, flexible and expandable lending choices.

Target Market(s)

Trucking Companies

Industry/Entity Type

Trucking Company

Contact Information for Business Card

* $250,000 Application only Program
* Loans from $30,000 to 5,000,000
* Competitive Interest Rates

Font styles to use
Serif
Sans Serif

Colors

Designer to choose colors to be used in the design.

Requirements
Must have
• On the back of the card.
• * $250,000 Application only Program
• * Loans from $30,000 to 5,000,000
• My name, email, website. address
• * Competitive Interest Rates
• * 100% Financing
Nice to have
• I want my logo to pop on the card
• My logo is the great one I would like to use
Should not have
• I am up for your creativity as well

```html
<!DOCTYPE html>
<html lang="en">
<head>
<meta charset="utf-8">
<title>Summit Lending – Business Card</title>
<link rel="stylesheet" href="https://fonts.googleapis.com/css2?family=Archivo:wght@500;700;800;900&display=swap">
<style>
  :root {
    --bg: #e4e4e6;
    --orange: #e8551f;
    --orange-deep: #c9451a;
    --charcoal: #232425;
    --charcoal-soft: #36383a;
    --white: #ffffff;
    --line-grey: #d9d9db;
  }
  * { box-sizing: border-box; margin: 0; padding: 0; }
  html, body { width: 1200px; height: 799px; overflow: hidden; background: var(--bg); }
  body { position: relative; font-family: "Archivo", Arial, sans-serif; color: var(--white); }

  .card {
    position: absolute;
    width: 540px; height: 309px;
    overflow: hidden;
    box-shadow: 0 8px 22px rgba(0,0,0,.18);
  }
  .card svg.card-art { position: absolute; inset: 0; width: 100%; height: 100%; }
  .card-front { left: 40px; top: 245px; }
  .card-back  { left: 620px; top: 245px; background: var(--charcoal); }

  .brand {
    position: absolute;
    display: flex; align-items: center; gap: 8px;
    font-weight: 800; font-size: 17px; letter-spacing: .04em; text-transform: uppercase;
    color: var(--white);
    white-space: nowrap;
  }
  .brand-dot { width: 26px; height: 26px; border-radius: 50%; background: var(--white); flex: none; }
  .card-front .brand { left: 265px; top: 26px; }
  .card-back .brand { left: 30px; top: 118px; font-size: 14px; }
  .card-back .brand-dot { width: 22px; height: 22px; }

  .offer { position: absolute; text-transform: uppercase; font-weight: 800; line-height: 1.05; white-space: nowrap; }
  .offer .amount { font-size: 20px; font-weight: 900; }
  .offer .label { font-size: 12px; font-weight: 700; }

  .card-front .offer { left: 40px; top: 150px; }
  .card-front .offer .gap { height: 14px; }
  .card-front .offer .rates { margin-top: 14px; }

  .card-back .offer { right: 46px; top: 18px; text-align: right; }
  .card-back .offer .amount { color: var(--orange); font-size: 18px; }
  .card-back .offer .gap { height: 14px; }
  .card-back .offer .rates { margin-top: 16px; }

  .holder { position: absolute; left: 30px; top: 152px; text-transform: uppercase; white-space: nowrap; }
  .holder-name { font-size: 22px; font-weight: 900; letter-spacing: .02em; }
  .holder-title { font-size: 10px; font-weight: 700; letter-spacing: .06em; margin-top: 4px; }

  .contact { position: absolute; right: 52px; top: 170px; text-align: right; font-size: 11.5px; font-weight: 700; line-height: 24px; white-space: nowrap; }
  .address { position: absolute; right: 24px; top: 272px; font-size: 11.5px; font-weight: 700; white-space: nowrap; }
  .contact-icons { position: absolute; right: 18px; top: 172px; width: 22px; height: 74px; }
</style>
</head>
<body>

<!-- Front -->
<section class="card card-front" aria-label="Card front">
  <svg class="card-art" viewBox="0 0 540 309">
    <defs>
      <linearGradient id="loaderTone" x1="0" y1="0" x2="1" y2="1">
        <stop offset="0" stop-color="#d8572a"/>
        <stop offset="1" stop-color="#b24a24"/>
      </linearGradient>
      <linearGradient id="truckTone" x1="0" y1="0" x2="1" y2="1">
        <stop offset="0" stop-color="#2d2e30"/>
        <stop offset="1" stop-color="#4a4b4d"/>
      </linearGradient>
    </defs>
    <rect width="540" height="309" fill="var(--orange)"/>
    <rect x="0" y="0" width="300" height="170" fill="url(#loaderTone)" opacity=".55" role="img" aria-label="Faded photo of a wheel loader on a job site"/>
    <path d="M176 0 H540 V262 C455 246 320 214 250 140 C214 100 190 52 176 0Z" fill="var(--line-grey)"/>
    <path d="M196 0 H540 V244 C460 228 335 198 268 128 C234 92 210 48 196 0Z" fill="url(#truckTone)" role="img" aria-label="Dark photo of a heavy-duty truck"/>
    <path d="M0 248 C60 284 130 300 210 309 H0Z" fill="var(--white)"/>
  </svg>
  <div class="brand"><span class="brand-dot"></span>Summit Lending</div>
  <div class="offer">
    <div class="amount">$250,000</div>
    <div class="label">Application only program</div>
    <div class="gap"></div>
    <div class="label">Loans from</div>
    <div class="amount">$30,000 to 5,000,000</div>
    <div class="label rates">Competitive interest rates</div>
  </div>
</section>

<!-- Back -->
<section class="card card-back" aria-label="Card back">
  <svg class="card-art" viewBox="0 0 540 309">
    <defs>
      <linearGradient id="slateTone" x1="0" y1="0" x2="1" y2="1">
        <stop offset="0" stop-color="#2b2c2e"/>
        <stop offset=".6" stop-color="#3a3c3e"/>
        <stop offset="1" stop-color="#2a2b2c"/>
      </linearGradient>
    </defs>
    <path d="M0 0 H190 C262 70 262 220 170 309 H0Z" fill="url(#slateTone)" role="img" aria-label="Dark slate texture"/>
    <path d="M198 6 C270 76 270 224 176 306" fill="none" stroke="var(--orange)" stroke-width="7"/>
    <path d="M540 150 V296 H430Z" fill="var(--orange)"/>
    <path d="M290 309 L306 294 H540 V309Z" fill="var(--white)"/>
    <path d="M200 309 L214 296 H300 L286 309Z" fill="var(--orange)"/>
  </svg>
  <svg class="contact-icons" viewBox="0 0 22 74" aria-hidden="true">
    <rect x="6" y="0" width="9" height="14" rx="2" fill="none" stroke="#fff" stroke-width="1.5"/>
    <circle cx="10.5" cy="34" r="6.5" fill="none" stroke="#fff" stroke-width="1.5"/>
    <path d="M4 34 H17 M10.5 27.5 V40.5" stroke="#fff" stroke-width="1"/>
    <path d="M10.5 70 C6 64 5 61 5 59 A5.5 5.5 0 0 1 16 59 C16 61 15 64 10.5 70Z" fill="none" stroke="#fff" stroke-width="1.5"/>
    <circle cx="10.5" cy="59" r="1.8" fill="#fff"/>
  </svg>
  <div class="brand"><span class="brand-dot"></span>Summit Lending</div>
  <div class="holder">
    <div class="holder-name">Mark Delaney</div>
    <div class="holder-title">Marketing Executive</div>
  </div>
  <div class="offer">
    <div class="amount">$250,000</div>
    <div class="label">Application only program</div>
    <div class="gap"></div>
    <div class="label">Loans from</div>
    <div class="amount">$30,000 to 5,000,000</div>
    <div class="label rates">Competitive interest rates</div>
  </div>
  <div class="contact">
    <div>Cell: 555-014-2290</div>
    <div>Website: summitlendco.com</div>
    <div>Email: mark@summitlendco.com</div>
  </div>
  <div class="address">1270 Ridgefield Lane, Oak Harbor, IL 60099</div>
</section>

</body>
</html>
```